Business Card Design

We are a commercial real estate brokerage in San Francisco, leasing office buildings downtown.
I would like a clean, elegant look. Simple but powerful .

Industry/Entity Type

Business

Contact Information for Business Card

Derek Holloway
lic# 07258143
415.555.0172
derek@velt-commercial.example
velt-commercial.example

```html
<!DOCTYPE html>
<html lang="en">
<head>
<meta charset="utf-8">
<title>Velt Commercial — Business Card</title>
<link rel="stylesheet" href="https://fonts.googleapis.com/css2?family=Arimo:wght@400;700&display=swap">
<style>
  :root {
    --backdrop: #2e2f31;
    --card: #ffffff;
    --accent: #7d91b0;
    --ink: #4a4d52;
    --ink-soft: #6b6e73;
    --city-light: #c9ccd1;
    --city-dark: #55585d;
  }
  * { box-sizing: border-box; margin: 0; padding: 0; }
  html, body {
    width: 1200px; height: 950px; overflow: hidden;
    background: var(--backdrop);
    font-family: "Arimo", Arial, sans-serif;
  }
  .stage {
    position: relative; width: 1200px; height: 950px;
    display: flex; flex-direction: column; align-items: center;
    justify-content: center; gap: 50px;
  }
  .card {
    position: relative; width: 700px; height: 400px;
    background: var(--card);
    box-shadow: 0 10px 24px rgba(0,0,0,.45);
    overflow: hidden;
  }
  /* Back side */
  .card-back { display: flex; flex-direction: column; align-items: center; }
  .skyline-art {
    margin-top: 95px; width: 220px; height: 120px;
    background: linear-gradient(180deg, var(--city-light) 0%, #8d9096 55%, var(--city-dark) 100%);
  }
  .tagline {
    margin-top: 34px; text-align: center;
    font-size: 17px; line-height: 1.4; color: var(--ink-soft);
  }
  /* Front side */
  .accent-band {
    position: absolute; left: 0; top: 0; bottom: 0; width: 190px;
    background: var(--accent);
  }
  .brand {
    position: absolute; left: 110px; top: 118px;
    display: flex; align-items: center;
  }
  .brand-art {
    width: 120px; height: 80px;
    background: linear-gradient(180deg, var(--city-light) 0%, #8d9096 55%, var(--city-dark) 100%);
  }
  .brand-divider {
    width: 2px; height: 96px; margin: 0 14px 0 16px; background: var(--ink);
  }
  .brand-name {
    color: var(--accent); font-weight: 400; line-height: 1;
  }
  .brand-name .brand-word { display: block; font-size: 56px; letter-spacing: 1px; }
  .brand-name .brand-sub { display: block; font-size: 22px; letter-spacing: 1.5px; margin-top: 4px; }
  .contact {
    position: absolute; left: 262px; top: 236px; color: var(--ink);
  }
  .contact-name { font-size: 24px; color: var(--accent); margin-bottom: 10px; }
  .contact-line {
    display: flex; align-items: center; gap: 10px;
    font-size: 19px; line-height: 1.45; color: var(--ink-soft);
  }
  .contact-line svg { width: 16px; height: 16px; fill: var(--ink); flex: none; }
  .licence { margin-bottom: 4px; }
</style>
</head>
<body>
<main class="stage">
  <section class="card card-back" aria-label="Card back">
    <div class="skyline-art" role="img" aria-label="Illustration of downtown office towers"></div>
    <p class="tagline">commercial real estate brokerage in San Francisco<br>leasing office buildings downtown.</p>
  </section>

  <section class="card card-front" aria-label="Card front">
    <div class="accent-band"></div>
    <div class="brand">
      <div class="brand-art" role="img" aria-label="Office tower illustration beside the company name"></div>
      <div class="brand-divider"></div>
      <div class="brand-name">
        <span class="brand-word">VELT</span>
        <span class="brand-sub">COMMERCIAL</span>
      </div>
    </div>
    <div class="contact">
      <p class="contact-name">Derek Holloway</p>
      <p class="contact-line licence">lic# 07258143</p>
      <p class="contact-line">
        <svg viewBox="0 0 16 16" aria-hidden="true"><path d="M3 1h3l1.5 4-2 1.2a9 9 0 0 0 4.3 4.3L11 8.5l4 1.5v3a2 2 0 0 1-2 2A12 12 0 0 1 1 3a2 2 0 0 1 2-2z"/></svg>
        415.555.0172
      </p>
      <p class="contact-line">
        <svg viewBox="0 0 16 16" aria-hidden="true"><path d="M1 3h14v10H1z" fill="none" stroke="currentColor"/><path d="M1 3h14v1.5L8 9 1 4.5z"/></svg>
        derek@velt-commercial.example
      </p>
      <p class="contact-line">
        <svg viewBox="0 0 16 16" aria-hidden="true"><path d="M8 1a5 5 0 0 1 5 5c0 4-5 9-5 9S3 10 3 6a5 5 0 0 1 5-5zm0 3a2 2 0 1 0 0 4 2 2 0 0 0 0-4z"/></svg>
        velt-commercial.example
      </p>
    </div>
  </section>
</main>
</body>
</html>
```